Moxy Fen needs some awesome stationary

Do you have what it takes to get my brand? You either do or you don't, have a crack at a design and you my just win my business.

I don't want to waste your or my time, so put your creative genius on either a business card or envelope.

I however need a package of stationary that follows the same brand. I will message you to complete the remaining should I like your first submission.

Here is what I need, have a go!

Basically I need the following for my small business based in melbourne.
- Letterhead (printer ready and MS Word)
- Business Card
- Compliments Slip
- Envelope
- Proposal Cover Page (MS Word only)
- Presentation Folder
- Marbled Fox Cards
- Student Name Tent
- Index Cards
- Vell-Ka

I am establishing the brand and it must be modern, professional but also relaxed; that is not formal and not corporate. It represents a company are leaders, but small enough to care and operate like a bunch of friends. We are bringing people and conversations back to business, and turfing out all the bureaucracy and crazy and wasteful procedures. Its about "lets talk and figure it out together and find even better ways".

Target Market(s)

Mainly companies that build software products, but Agile practices are used in many other industries (even graphic design projects)

Industry/Entity Type

Information Technology

Font styles to use
Sans Serif

Colors
3176b5
aaaaaa

Requirements
Must have
• I like curves and circles and not boxes or rectangles.
• I want a colour rich design with my brand colours, but it must be balanced.
• I want more modern than traditional, but simple modern
Should not have
• Not corporate
• Please don't waste my time if your not going to think about it.
• Don't mess with my primary logo
• Don't change my colours
• Don't overlay logo on image

```html
<!DOCTYPE html>
<html lang="en">
<head>
<meta charset="utf-8">
<title>Moxy Fen stationery</title>
<link rel="stylesheet" href="https://fonts.googleapis.com/css2?family=Ubuntu:wght@400;500;700&family=Open+Sans:wght@400;600&family=Pinyon+Script&display=swap">
<style>
:root{
  --brand-blue:#385d98;
  --brand-grey:#8a94a6;
  --paper:#f1f1f2;
  --bg:#e4e4e5;
  --ink:#4a4f59;
  --card-grey:#6b7171;
  --card-purple:#682a80;
  --card-pink:#c2306c;
  --card-sky:#5ab4ee;
  --card-royal:#1f44a8;
}
*{box-sizing:border-box;margin:0;padding:0}
html,body{width:1121px;height:1200px;overflow:hidden}
body{background:var(--bg);font-family:"Open Sans",sans-serif;color:var(--ink);position:relative}
.item{position:absolute;background:var(--paper);box-shadow:0 2px 5px rgba(0,0,0,.18)}
.brand{font-family:"Ubuntu",sans-serif;font-weight:700;color:var(--brand-blue);white-space:nowrap;display:flex;align-items:center;gap:.3em}
.brand .dot{display:inline-block;width:1em;height:1em;border-radius:50%;background:var(--brand-blue)}
.fine{font-size:4.6px;line-height:1.45;color:var(--ink)}

/* business cards */
.bcard-front{left:157px;top:348px;width:133px;height:74px;overflow:hidden}
.bcard-front svg{position:absolute;inset:0}
.bcard-front .details{position:absolute;left:8px;top:12px;color:#fff;font-size:3.8px;line-height:1.45}
.bcard-front .details strong{font-size:4.6px;display:block}
.bcard-front .brand{position:absolute;right:8px;top:42px;font-size:8.5px}
.bcard-back{left:157px;top:445px;width:133px;height:75px;background:var(--brand-blue);display:flex;flex-direction:column;align-items:center;justify-content:center;gap:14px}
.bcard-back .brand{color:#fff;font-size:11px}
.bcard-back .url{color:#dfe6f2;font-size:3.6px;letter-spacing:1.2px}

/* letterhead */
.letterhead{left:326px;top:104px;width:293px;height:416px}
.letterhead .brand{position:absolute;left:28px;top:50px;font-size:9px}
.letterhead .address{position:absolute;right:102px;top:34px;text-align:right}
.letterhead .contact{position:absolute;left:205px;top:28px;padding-left:5px;border-left:.6px solid #999}

/* folder */
.folder{left:658px;top:84px;width:346px;height:438px;overflow:hidden;background:#e7e9ec}
.folder svg{position:absolute;inset:0}
.folder .brand{position:absolute;left:0;right:0;top:160px;justify-content:center;font-size:30px}
.folder .url{position:absolute;left:0;right:0;bottom:50px;text-align:center;color:#fff;font-size:10px}

/* envelopes & slip */
.envelope-back{left:44px;top:563px;width:329px;height:156px}
.envelope-back .brand{position:absolute;left:19px;top:30px;font-size:8px}
.envelope-back .fine{position:absolute;left:19px;top:46px}
.envelope-flap{left:405px;top:563px;width:328px;height:156px;overflow:hidden}
.envelope-flap svg{position:absolute;inset:0}
.envelope-flap .brand{position:absolute;left:0;right:0;top:16px;justify-content:center;color:#fff;font-size:7px}
.envelope-flap .url{position:absolute;left:0;right:0;top:33px;text-align:center;color:#dfe6f2;font-size:3.6px}
.comp-slip{left:761px;top:563px;width:329px;height:156px}
.comp-slip .brand{position:absolute;left:16px;top:30px;font-size:8px}
.comp-slip .footer{position:absolute;left:16px;right:18px;top:121px;border-bottom:.6px solid #8a94a6;padding-bottom:1px;font-size:3.8px;color:var(--ink)}
.comp-slip .url{position:absolute;left:16px;top:137px;font-size:3.8px;color:var(--brand-blue)}
.comp-slip .greeting{position:absolute;right:20px;top:113px;font-family:"Pinyon Script",cursive;font-size:17px;color:var(--brand-blue)}

/* notepad */
.notepad{left:63px;top:760px;width:245px;height:175px}
.notepad .spiral{position:absolute;left:2px;right:2px;top:-12px;height:14px;background:repeating-linear-gradient(90deg,#333 0 1.6px,transparent 1.6px 7.3px)}
.notepad .brand{position:absolute;left:18px;top:20px;font-size:12.5px}
.notepad .lines{position:absolute;left:15px;right:12px;top:52px;height:110px;background:repeating-linear-gradient(180deg,transparent 0 17.5px,#9aa0a8 17.5px 18.3px)}

/* name tent */
.name-tent{left:414px;top:795px;width:250px;height:86px;display:flex;align-items:center;justify-content:center}
.name-tent .brand{font-size:24px}

/* sticky note */
.sticky-note{left:820px;top:750px;width:178px;height:163px;background:linear-gradient(160deg,#e6c633,#dcc84e);transform:rotate(-3deg);box-shadow:0 8px 10px rgba(0,0,0,.22)}
.sticky-note .dot{position:absolute;left:39px;top:32px;width:100px;height:100px;border-radius:50%;background:rgba(255,255,255,.14)}

/* estimation cards */
.deck{position:absolute;top:953px;height:225px;width:145px;border-radius:4px;overflow:hidden;display:flex;align-items:center;justify-content:center;font-family:"Ubuntu",sans-serif;font-weight:700;font-size:66px;color:#fff}
.deck.title{left:32px;background:#fff;box-shadow:0 2px 5px rgba(0,0,0,.25);flex-direction:column}
.deck.title .brand{font-size:17px;position:absolute;top:60px}
.deck.title .label{position:absolute;bottom:20px;font-size:16px;font-weight:400;font-family:"Open Sans",sans-serif;color:var(--brand-blue)}
.deck.grey{left:194px;background:var(--card-grey)}
.deck.purple{left:348px;background:var(--card-purple)}
.deck.pink{left:501px;background:var(--card-pink)}
.deck.sky{left:654px;background:var(--card-sky)}
.deck.royal{left:803px;background:var(--card-royal)}
.deck.back{left:954px;background:#fff}
.deck.back svg{position:absolute;inset:0}
.deck.back .brand{position:absolute;left:0;right:0;top:168px;justify-content:center;color:#fff;font-size:19px}
.deck.back .phone{position:absolute;left:0;right:0;top:192px;text-align:center;color:#fff;font-size:12px;font-weight:400;letter-spacing:1.5px}
</style>
</head>
<body>

<section class="item bcard-front">
  <svg viewBox="0 0 133 74" width="133" height="74"><path d="M0 0H76C62 20 62 56 90 74H0Z" fill="var(--brand-blue)"/><path d="M76 0C66 22 68 55 90 74H100C78 58 70 26 80 0Z" fill="var(--brand-grey)"/></svg>
  <div class="details"><strong>DALE KORRIN</strong>CEO<br>Professional Scrum Trainer<br><br>PO Box 4810<br>Ashwood Vale<br>VIC 3190, Australia<br><br>+61 400 555 019<br>dale@moxyfen.example<br>www.moxyfen.example</div>
  <div class="brand">Moxy Fen</div>
</section>

<section class="item bcard-back">
  <div class="brand"><span class="dot"></span>Moxy Fen</div>
  <div class="url">www.moxyfen.example</div>
</section>

<section class="item letterhead">
  <div class="brand"><span class="dot"></span>Moxy Fen</div>
  <div class="fine address">PO Box 4810<br>Ashwood Vale<br>VIC 3190 Australia</div>
  <div class="fine contact">Moxy Fen<br>ABN 4471 2093<br>1300 555 019<br>www.moxyfen.example</div>
</section>

<section class="item folder">
  <svg viewBox="0 0 346 438" width="346" height="438"><path d="M0 245C60 300 130 325 200 318C270 310 320 280 346 246V438H0Z" fill="var(--brand-blue)"/><path d="M150 318C250 320 330 250 346 110V185C318 275 255 312 150 318Z" fill="var(--brand-grey)"/><rect x="6" y="0" width="1.2" height="438" fill="rgba(0,0,0,.12)"/></svg>
  <div class="brand"><span class="dot"></span>Moxy Fen</div>
  <div class="url">www.moxyfen.example</div>
</section>

<section class="item envelope-back">
  <div class="brand"><span class="dot"></span>Moxy Fen</div>
  <div class="fine">PO Box 4810<br>Ashwood Vale<br>VIC 3190, Australia<br><br>1300 555 019</div>
</section>

<section class="item envelope-flap">
  <svg viewBox="0 0 328 156" width="328" height="156"><path d="M0 0H328L322 50Q320 55 314 55H14Q8 55 6 50Z" fill="var(--brand-blue)"/></svg>
  <div class="brand">Moxy Fen</div>
  <div class="url">www.moxyfen.example</div>
</section>

<section class="item comp-slip">
  <div class="brand"><span class="dot"></span>Moxy Fen</div>
  <div class="greeting">With Compliments</div>
  <div class="footer">PO Box 4810, Ashwood Vale, VIC 3190, Australia<br>P: 1300 555 019 M: +61 400 555 019 E: dale@moxyfen.example</div>
  <div class="url">www.moxyfen.example</div>
</section>

<section class="item notepad">
  <div class="spiral"></div>
  <div class="brand"><span class="dot"></span>Moxy Fen</div>
  <div class="lines"></div>
</section>

<section class="item name-tent">
  <div class="brand"><span class="dot"></span>Moxy Fen</div>
</section>

<section class="item sticky-note" aria-label="Vell-Ka note">
  <span class="dot"></span>
</section>

<section class="deck title">
  <div class="brand"><span class="dot"></span>Moxy Fen</div>
  <div class="label">Marbled Fox card</div>
</section>
<section class="deck grey">0</section>
<section class="deck purple">1/2</section>
<section class="deck pink">1</section>
<section class="deck sky">3</section>
<section class="deck royal">5</section>
<section class="deck back">
  <svg viewBox="0 0 145 225" width="145" height="225"><path d="M0 120C30 165 80 180 145 150V225H0Z" fill="var(--brand-blue)"/></svg>
  <div class="brand">Moxy Fen</div>
  <div class="phone">1300 555 019</div>
</section>

</body>
</html>
```